GJ & DW Fencing Pty Ltd

We already have an existing logo created by Pixel Harbour however we have restructured to a company. We would like someone to add Pty Ltd to our business name please.

Colors

Designer to choose only greyscale colors for use in the design.

```html
<!DOCTYPE html>
<html lang="en">
<head>
<meta charset="utf-8">
<title>GJ &amp; DW Fencing Pty Ltd — Business Card</title>
<link rel="stylesheet" href="https://fonts.googleapis.com/css2?family=Merriweather:wght@400;700&display=swap">
<style>
  :root {
    --page: #3a3a3c;
    --card: #1f2122;
    --ink: #f4f4f4;
    --ink-soft: #c9c9c9;
    --rule: #8a8a8a;
  }
  * { box-sizing: border-box; margin: 0; padding: 0; }
  html, body {
    width: 1200px; height: 800px; overflow: hidden;
    background: var(--page);
    font-family: "Merriweather", Georgia, serif;
    color: var(--ink);
  }
  .stage {
    width: 1200px; height: 800px;
    display: flex; align-items: center; justify-content: center; gap: 40px;
  }
  .card {
    width: 520px; height: 298px;
    background: var(--card);
    border-radius: 4px;
    box-shadow: 0 14px 30px rgba(0,0,0,.35);
    position: relative;
  }
  .wordmark {
    display: flex; align-items: center; gap: 12px;
    font-weight: 700; color: var(--ink);
    line-height: 1.05; letter-spacing: .5px;
  }
  .wordmark-dot {
    width: 46px; height: 46px; border-radius: 50%;
    background: var(--ink); flex: none;
  }
  .wordmark-name { font-size: 26px; }
  .card-front { display: flex; align-items: center; justify-content: center; }
  .card-front .wordmark-name { font-size: 30px; }
  .card-back { display: flex; align-items: center; padding: 0 30px; }
  .card-back .wordmark-name { font-size: 19px; }
  .card-back .wordmark-dot { width: 34px; height: 34px; }
  .divider {
    width: 1px; height: 130px; background: var(--rule);
    margin: 0 22px 0 18px; flex: none;
  }
  .contact { font-size: 11px; color: var(--ink-soft); }
  .contact-name { font-size: 13px; font-weight: 700; color: var(--ink); letter-spacing: .5px; }
  .contact-role { margin-bottom: 12px; }
  .contact-line { display: flex; align-items: center; gap: 7px; margin-bottom: 5px; }
  .contact-icon {
    width: 14px; height: 14px; border-radius: 50%; background: var(--ink);
    display: flex; align-items: center; justify-content: center; flex: none;
  }
  .contact-company { font-weight: 700; color: var(--ink); margin-top: 10px; }
</style>
</head>
<body>
<main class="stage">
  <section class="card card-front">
    <div class="wordmark">
      <span class="wordmark-dot"></span>
      <span class="wordmark-name">GJ &amp; DW Fencing<br>Pty Ltd</span>
    </div>
  </section>

  <section class="card card-back">
    <div class="wordmark">
      <span class="wordmark-dot"></span>
      <span class="wordmark-name">GJ &amp; DW Fencing<br>Pty Ltd</span>
    </div>
    <span class="divider"></span>
    <div class="contact">
      <p class="contact-name">LIAM CARTER</p>
      <p class="contact-role">President</p>
      <p class="contact-line">
        <span class="contact-icon">
          <svg width="8" height="8" viewBox="0 0 24 24"><path fill="#1f2122" d="M6.6 10.8a15.1 15.1 0 006.6 6.6l2.2-2.2c.3-.3.7-.4 1-.2 1.1.4 2.3.6 3.6.6.6 0 1 .4 1 1V20c0 .6-.4 1-1 1A17 17 0 013 4c0-.6.4-1 1-1h3.5c.6 0 1 .4 1 1 0 1.3.2 2.5.6 3.6.1.3 0 .7-.2 1z"/></svg>
        </span>
        Mob 0400 123 456
      </p>
      <p class="contact-line">
        <span class="contact-icon">
          <svg width="8" height="8" viewBox="0 0 24 24"><path fill="#1f2122" d="M2 5h20v14H2z"/><path fill="none" stroke="#f4f4f4" stroke-width="2" d="M2 5l10 8 10-8"/></svg>
        </span>
        gjdwfencing@mailbox.com
      </p>
      <p class="contact-company">GJ &amp; DW Fencing Pty Ltd</p>
      <p>PO Box 215 Eastvale WA 6999</p>
    </div>
  </section>
</main>
</body>
</html>
```